Lurvik.no is a new website about pedagogical entrepreneurship. It's main target group is teachers. The Nordic Bureau for Digital Schooling and the National Office for Learning and Classrooms are leading the project.

The web page is meant to show examples of how different methods of entrepreneurship can be used pedagogical in a learning environment. The page will also support the user with examples of different teaching programs and other examples of best practice.

Pedagogical entrepreneurship is not about business and men in suits. It's a method for learning. The focus in the design should be on school, education and new ways of learning.

The final product should be motivating and engaging, but at the same time governmental and serious. We are not looking for something "flashy" and corporate-looking, but a moderate, task-focused and clean design that state quality.

We need designs for three pages:
1 - frontpage
2 - subpage ("Metoder og undervisningsopplegg")
3 - subpage ("Små-TOPP i Vassbygd")

The interaction design for these three pages will be uploaded as an attachment.

We would like you to find inspiration in the following websites:
- www.skapekraft.no
- www.giellu.no
- www.brightfernlab.com
- www.zyx.no
(more will be added)

Please use the attached logo, and feel free to use this as an inspiration for the rest of the design.

Target Market(s)

Teachers

Industry/Entity Type

Education

Requirements
Must have
• * Header with: Logo. Main navigation. Utility navigation. Search box.
* Footer
Should not have
• Images of men in suits.
Very strong graphical elements that stands out too much (we want it clean).

```html
<!DOCTYPE html>
<html lang="en">
<head>
<meta charset="utf-8">
<title>Good Examples – Lurvik.no</title>
<link href="https://fonts.googleapis.com/css2?family=Bree+Serif&family=Arimo:wght@400;700&display=swap" rel="stylesheet">
<style>
:root{
  --navy:#1d3560;
  --navy-dark:#0f2547;
  --blue:#1a7fc4;
  --heading-blue:#1a4f86;
  --green:#7ab317;
  --text:#3a3a3a;
  --muted:#555;
  --panel-bg:#f4f4f4;
}
*{box-sizing:border-box;margin:0;padding:0}
html,body{width:960px;height:1200px;overflow:hidden;background:#fff}
body{position:relative;font-family:"Arimo",Arial,sans-serif;color:var(--text)}
.abs{position:absolute}

.utility-bar{left:0;top:0;width:960px;height:30px;background:var(--navy)}
.utility-nav{right:303px;top:9px;display:flex;gap:24px;font-size:10px;color:#fff}
.search-box{left:686px;top:6px;width:178px;height:18px;background:#fff;border-radius:9px;font-size:9px;color:#888;padding:3px 8px}
.search-box svg{position:absolute;right:6px;top:3px}

.logo{left:96px;top:46px;display:flex;align-items:center;gap:12px}
.logo-dot{width:44px;height:44px;border-radius:50%;background:var(--blue)}
.logo-name{font-family:"Bree Serif",serif;font-size:40px;color:var(--blue);line-height:1}
.main-nav{top:58px;display:flex}
.main-nav a{display:block;font-size:10.5px;line-height:16px;color:#333;text-decoration:none;border-left:2px solid var(--blue);padding:0 0 14px 10px;height:42px}
.main-nav a.active{color:var(--blue);border-left-color:var(--green)}

.banner{left:0;top:114px;width:960px;height:92px;
  background-image:linear-gradient(rgba(255,255,255,.06) 1px,transparent 1px),linear-gradient(90deg,rgba(255,255,255,.06) 1px,transparent 1px),linear-gradient(#2a8fd2,#1877bd);
  background-size:8px 8px,8px 8px,100% 100%}
.banner h1{position:absolute;left:98px;top:30px;font-family:"Bree Serif",serif;font-weight:400;font-size:29px;color:#fff}

.breadcrumb{left:95px;top:221px;font-size:8.5px;color:#222;display:flex;gap:12px}
.breadcrumb a{color:var(--heading-blue);text-decoration:none}
.share{top:219px;display:flex;font-size:8.5px}
.share .btn{border:1px solid #ccc;border-radius:2px;padding:2px 4px;background:#f6f6f6;display:flex;align-items:center;gap:3px;color:#333}
.share .btn i{display:block;width:9px;height:9px;background:var(--heading-blue)}
.share .count{border:1px solid #ccc;border-radius:2px;padding:2px 3px;margin-left:3px;background:#fff}
.dash{left:95px;width:767px;border-top:1px dashed #999}
.dash.green{border-top-color:var(--green)}

.title{left:94px;top:268px;font-family:"Bree Serif",serif;font-size:19.5px;color:var(--green);font-weight:400}
.lead{left:95px;top:306px;width:460px;font-size:12px;line-height:16px;font-weight:700;color:#222}
.body-text{width:452px;font-size:10px;line-height:16px;color:var(--muted)}
.subhead{font-size:11.5px;font-weight:700;color:#222}

.fact{display:flex;align-items:center;gap:8px}
.fact-icon{width:48px;height:48px;border-radius:50%;background:#fff;border:1px solid #ddd;display:flex;align-items:center;justify-content:center;box-shadow:0 1px 2px rgba(0,0,0,.15)}
.fact-icon span{width:40px;height:40px;border-radius:50%;background:radial-gradient(circle at 50% 35%,#2d6fb0,var(--navy-dark));display:flex;align-items:center;justify-content:center}
.fact-label{font-size:12.5px;color:#333}
.fact-value{font-size:9.5px;font-weight:700;color:var(--green);margin-top:2px}

.card-frame{border:1px solid #ddd;border-radius:5px;background:#fff;padding:4px;box-shadow:0 1px 3px rgba(0,0,0,.08)}
.card-inner{width:100%;height:100%;border-radius:3px;background:linear-gradient(#1f7dc2,#123b6b 75%,#0f2b52);position:relative}
.school{left:654px;top:305px;width:208px;height:229px}
.school-name{position:absolute;left:60px;top:13px;color:#fff;font-size:12px}
.school-name small{display:block;font-size:8px;font-weight:700;margin-top:2px}
.school-photo{position:absolute;left:15px;top:44px;width:169px;height:95px;border:1px solid #cfe0ee;background:linear-gradient(#c9d3db 0 30%,#8a8478 50%,#e8ecef 85%)}
.contact{position:absolute;left:16px;top:149px;width:168px;height:58px;background:#fff;border-radius:2px}
.contact b{position:absolute;left:44px;top:9px;font-size:9px;font-weight:700;color:#444}
.contact span{position:absolute;left:44px;top:24px;font-size:11.5px;color:var(--green)}

.media{left:566px;top:590px;width:294px;height:308px}
.media h2{position:absolute;left:56px;top:17px;font-family:"Bree Serif",serif;font-weight:400;font-size:14px;color:#fff}
.tabs{position:absolute;left:19px;top:42px;display:flex;font-size:10px;font-weight:700;color:#222}
.tabs div{background:#fff;padding:6px 10px;height:24px;margin-right:1px}
.tabs div+div{background:#f0f0f0}
.media-body{position:absolute;left:19px;top:66px;width:256px;height:222px;background:var(--panel-bg)}
.video{position:absolute;left:11px;top:14px;width:233px;height:129px;background:linear-gradient(#7d9a98,#4d6866 45%,#1d3b3f 70%,#10262a)}
.video-bar{position:absolute;left:0;bottom:0;width:100%;height:14px;background:rgba(0,0,0,.55)}
.video-link{position:absolute;left:11px;top:160px;font-size:10px;font-weight:700;color:#333;text-decoration:underline}
.video-note{position:absolute;left:11px;top:177px;font-size:10px;color:#444}

.related-band{left:0;top:1006px;width:960px;height:194px;background:linear-gradient(#e3eef8,#fff 80%);border-top:1px solid #cfd9e2}
.related-title{left:98px;top:966px;font-family:"Bree Serif",serif;font-size:20px;color:var(--heading-blue);font-weight:400}
.related-intro{left:98px;top:1018px;width:200px;font-size:11.5px;line-height:17.5px;color:#555}
.related-item{top:952px;width:170px}
.related-photo{width:108px;height:108px;border-radius:50%;border:3px solid var(--blue);background:radial-gradient(circle,#9a9a9a,#3c3c3c)}
.related-item b{display:block;margin-top:14px;font-family:"Bree Serif",serif;font-weight:400;font-size:12px;color:var(--heading-blue)}
.related-item span{display:block;font-size:11.5px;color:#555;margin-top:3px}
</style>
</head>
<body>

<div class="abs utility-bar"></div>
<nav class="abs utility-nav"><span>Home</span><span>Best Practices Schools</span><span>Lurvikometer</span><span>About Lurvik.no</span></nav>
<div class="abs search-box">search
  <svg width="11" height="11" viewBox="0 0 11 11"><circle cx="4.5" cy="4.5" r="3.3" fill="none" stroke="#7ab317" stroke-width="1.6"/><line x1="7" y1="7" x2="10" y2="10" stroke="#7ab317" stroke-width="1.8"/></svg>
</div>

<div class="abs logo"><div class="logo-dot"></div><div class="logo-name">Lurvik</div></div>
<nav>
  <div class="abs main-nav" style="left:390px"><a style="width:150px">What is pedagogical entrepreneurship?</a></div>
  <div class="abs main-nav" style="left:569px"><a style="width:128px">Methods and teaching plans</a></div>
  <div class="abs main-nav" style="left:738px"><a class="active" style="width:130px">Good examples / best practice</a></div>
</nav>

<header class="abs banner"><h1>Good Examples &amp; Best Practices</h1></header>

<div class="abs breadcrumb"><a>Home</a><span>&gt;</span><a>Good Examples</a><span>&gt;</span><span>Små-TOPP i Vassbygd</span></div>
<div class="abs share" style="left:727px"><div class="btn"><i></i>Like</div><div class="count">86</div></div>
<div class="abs share" style="left:798px"><div class="btn"><i style="border-radius:50%;background:#2aa3e0"></i>Share</div><div class="count">30</div></div>
<div class="abs dash" style="top:246px"></div>

<h2 class="abs title">Små-TOPP i Vassbygd</h2>
<p class="abs lead">Lorem ipsum dolor sit amet, consectetur adipiscing elit. Nam porttitor felis et elit egestas nec venenatis enim rhoncus.</p>
<p class="abs body-text" style="left:95px;top:346px">Maecenas lacus augue, dignissim vulputate eleifend vitae, scelerisque at sapien. Suspendisse diam felis, pulvinar vitae posuere eu, volutpat et urna. Vivamus vel leo justo, ut tincidunt ipsum. Curabitur justo orci, semper quis feugiat semper, dignissim a orci. Suspendisse nec ipsum sit amet nulla tincidunt vestibulum.</p>

<div class="abs fact" style="left:98px;top:430px">
  <div class="fact-icon"><span><svg width="24" height="24" viewBox="0 0 24 24"><circle cx="12" cy="12" r="8.5" fill="none" stroke="#fff" stroke-width="2"/><path d="M12 7v5l3 2" stroke="#fff" stroke-width="2" fill="none" stroke-linecap="round"/></svg></span></div>
  <div><div class="fact-label">Time Spent</div><div class="fact-value">Text</div></div>
</div>
<div class="abs fact" style="left:306px;top:430px">
  <div class="fact-icon"><span><svg width="24" height="24" viewBox="0 0 24 24"><rect x="4" y="6" width="13" height="13" rx="1.5" fill="none" stroke="#fff" stroke-width="2"/><path d="M10 14l9-9 2 2-9 9h-2z" fill="#fff"/></svg></span></div>
  <div><div class="fact-label">Subject</div><div class="fact-value">English, Norwegian, Maths</div></div>
</div>
<div class="abs fact" style="left:98px;top:496px">
  <div class="fact-icon"><span><svg width="24" height="24" viewBox="0 0 24 24"><circle cx="12" cy="5" r="2" fill="#fff"/><path d="M11 7L5 21M13 7l6 14M7 15h10" stroke="#fff" stroke-width="2" fill="none"/></svg></span></div>
  <div><div class="fact-label">Method</div><div class="fact-value">TOPP</div></div>
</div>

<aside class="abs card-frame school">
  <div class="card-inner">
    <svg style="position:absolute;left:18px;top:10px" width="30" height="26" viewBox="0 0 30 26"><path d="M2 12L15 2l13 10" stroke="#fff" stroke-width="2.5" fill="none"/><path d="M6 11v14h18V11L15 4z" fill="#fff"/><rect x="12" y="15" width="6" height="10" fill="#1a6fb0"/></svg>
    <div class="school-name">Vassbygd skole<small>4th Grade</small></div>
    <div class="school-photo" role="img" aria-label="Photo of the school building and playground in winter"></div>
    <div class="contact">
      <svg style="position:absolute;left:10px;top:11px" width="26" height="32" viewBox="0 0 26 32"><circle cx="13" cy="9" r="7" fill="#2a8fd2"/><path d="M1 31c0-9 5-14 12-14s12 5 12 14z" fill="#2a8fd2"/></svg>
      <b>Contact</b><span>Jane Doe</span>
    </div>
  </div>
</aside>

<div class="abs dash green" style="top:568px"></div>

<h3 class="abs subhead" style="left:95px;top:603px">This is how we did it</h3>
<p class="abs body-text" style="left:95px;top:630px">Maecenas lacus augue, dignissim vulputate eleifend vitae, scelerisque at sapien. Suspendisse diam felis, pulvinar vitae posuere eu, volutpat et urna. Vivamus vel leo justo, ut tincidunt ipsum. Curabitur justo orci, semper quis feugiat semper, dignissim a orci. Suspendisse nec ipsum sit amet nulla tincidunt vestibulum.</p>
<h3 class="abs subhead" style="left:95px;top:707px">Title</h3>
<p class="abs body-text" style="left:95px;top:734px">Maecenas lacus augue, dignissim vulputate eleifend vitae, scelerisque at sapien. Suspendisse diam felis, pulvinar vitae posuere eu, volutpat et urna. Vivamus vel leo justo, ut tincidunt ipsum. Curabitur justo orci, semper quis feugiat semper, dignissim a orci. Suspendisse nec ipsum sit amet nulla tincidunt vestibulum.</p>
<h3 class="abs subhead" style="left:95px;top:811px">Title</h3>
<p class="abs body-text" style="left:95px;top:838px">Maecenas lacus augue, dignissim vulputate eleifend vitae, scelerisque at sapien. Suspendisse diam felis, pulvinar vitae posuere eu, volutpat et urna. Vivamus vel leo justo, ut tincidunt ipsum. Curabitur justo orci, semper quis feugiat semper, dignissim a orci. Suspendisse nec ipsum sit amet nulla tincidunt vestibulum.</p>

<aside class="abs card-frame media">
  <div class="card-inner" style="background:linear-gradient(#1877bd,#123b6b 75%,#0d2748)">
    <svg style="position:absolute;left:20px;top:13px" width="30" height="22" viewBox="0 0 30 22"><circle cx="6" cy="5" r="3.5" fill="none" stroke="#fff" stroke-width="2"/><circle cx="15" cy="5" r="3.5" fill="none" stroke="#fff" stroke-width="2"/><rect x="2" y="10" width="18" height="11" fill="none" stroke="#fff" stroke-width="2"/><path d="M21 15l7-4v9l-7-4z" fill="#fff"/></svg>
    <h2>Multimedia</h2>
    <div class="tabs"><div>Videos (1)</div><div>Images (4)</div></div>
    <div class="media-body">
      <div class="video" role="img" aria-label="Video still of a stormy sea under a cloudy sky">
        <div class="video-bar"><svg style="position:absolute;left:12px;top:3px" width="8" height="8" viewBox="0 0 8 8"><path d="M1 0l6 4-6 4z" fill="#fff"/></svg><div style="position:absolute;left:32px;top:6px;width:160px;height:2px;background:#777"></div></div>
      </div>
      <div class="video-link">Ses video</div>
      <div class="video-note">Short text about the video</div>
    </div>
  </div>
</aside>

<div class="abs related-band"></div>
<h2 class="abs related-title">View More Like This</h2>
<p class="abs related-intro">Learn about some of the schools and systems that have incorporated pedagogical entrepreneurship best practices.</p>
<div class="abs related-item" style="left:374px">
  <div class="related-photo" role="img" aria-label="Photo of pupils working together around a table"></div>
  <b style="margin-left:13px">Små-TOPP</b><span style="margin-left:13px">at Vassbygd School</span>
</div>
<div class="abs related-item" style="left:547px">
  <div class="related-photo" role="img" aria-label="Photo of a young pupil holding a book"></div>
  <b style="margin-left:11px">Gründerleir</b><span style="margin-left:11px">at Strandvik School</span>
</div>
<div class="abs related-item" style="left:720px">
  <div class="related-photo" role="img" aria-label="Photo of a vaulted stone hallway"></div>
  <b style="margin-left:1px">Lærekroken</b><span style="margin-left:1px">at Fjellhavn School</span>
</div>

</body>
</html>
```